Carpet cleaning company focused on high quality needs business cards

We are a growing company that just merged with another company and need to design a new business card. We do both residential as well as commercial cleaning. We do carpet, tile & grout, upholstery, hard floors, and stain & pet odor removal. We treat our customers like family and strive to achieve outstanding results with every job.

```html
<!DOCTYPE html>
<html lang="en">
<head>
<meta charset="utf-8">
<title>Kinfolk Steam Care – Business Cards</title>
<link href="https://fonts.googleapis.com/css2?family=Poppins:wght@400;500;700;800&display=swap" rel="stylesheet">
<style>
  :root {
    --stage: #1d1d1f;
    --paper: #ffffff;
    --ink: #231f20;
    --band-dark: #232224;
    --accent: #ee4540;
    --on-dark: #ffffff;
  }
  * { box-sizing: border-box; margin: 0; padding: 0; }
  html, body { width: 1200px; height: 1015px; overflow: hidden; }
  body {
    background: var(--stage);
    font-family: "Poppins", sans-serif;
    position: relative;
  }
  .card {
    position: absolute;
    width: 600px;
    height: 343px;
    background: var(--paper);
    overflow: hidden;
    box-shadow: 0 18px 40px rgba(0,0,0,.55);
  }
  .card--front { left: 120px; top: 80px; }
  .card--back  { left: 480px; top: 560px; }

  .brand {
    position: absolute;
    left: 0; right: 0; top: 0;
    height: 190px;
    display: flex;
    align-items: center;
    justify-content: center;
    gap: 14px;
  }
  .brand__mark {
    width: 34px; height: 34px;
    background: var(--accent);
  }
  .brand__name {
    font-weight: 800;
    font-size: 38px;
    letter-spacing: -0.5px;
    color: var(--ink);
    line-height: 1;
  }

  .band {
    position: absolute;
    left: 0; right: 0; bottom: 0;
    height: 153px;
  }
  .card--front .band { background: var(--band-dark); color: var(--on-dark); text-align: center; padding-top: 30px; }
  .card--back  .band { background: var(--accent); color: var(--on-dark); }

  .services__heading {
    color: var(--accent);
    font-weight: 500;
    font-size: 17px;
    letter-spacing: .3px;
    margin-bottom: 10px;
  }
  .services__list {
    font-size: 16px;
    line-height: 1.45;
  }
  .dot { color: var(--accent); padding: 0 6px; }

  .contact-row {
    position: absolute;
    left: 40px; right: 30px; top: 22px;
    display: flex;
    align-items: center;
  }
  .person { width: 230px; }
  .person__name { font-weight: 700; font-size: 25px; line-height: 1.1; }
  .person__title { font-size: 15px; }
  .divider {
    width: 1px; height: 72px;
    background: rgba(255,255,255,.7);
    margin: 0 24px 0 10px;
  }
  .contacts { list-style: none; font-size: 14.5px; line-height: 1.6; }
  .contacts li { display: flex; align-items: center; gap: 10px; }
  .contacts svg { width: 15px; height: 15px; flex: none; }
  .address {
    position: absolute;
    left: 0; right: 0; bottom: 22px;
    text-align: center;
    font-size: 15px;
  }
</style>
</head>
<body>

  <section class="card card--front">
    <div class="brand">
      <span class="brand__mark"></span>
      <span class="brand__name">Kinfolk Steam Care</span>
    </div>
    <div class="band services">
      <p class="services__heading">RESIDENTIAL &amp; COMMERCIAL CLEANING</p>
      <p class="services__list">
        Carpet<span class="dot">•</span>Tile &amp; Grout<span class="dot">•</span>Upholstery<br>
        Hard floors &amp; Stain<span class="dot">•</span>Pet Odor Removal
      </p>
    </div>
  </section>

  <section class="card card--back">
    <div class="brand">
      <span class="brand__mark"></span>
      <span class="brand__name">Kinfolk Steam Care</span>
    </div>
    <div class="band">
      <div class="contact-row">
        <div class="person">
          <p class="person__name">Daniel Reyes</p>
          <p class="person__title">Managing Director</p>
        </div>
        <span class="divider"></span>
        <ul class="contacts">
          <li>
            <svg viewBox="0 0 16 16" aria-hidden="true"><path d="M3 1.5l2.5 0 1 3.5-1.6 1.2a9 9 0 0 0 4.9 4.9L11 9.5l3.5 1v2.5a1.5 1.5 0 0 1-1.5 1.5A12.5 12.5 0 0 1 1.5 3 1.5 1.5 0 0 1 3 1.5z" fill="#fff"/></svg>
            044-555 0182
          </li>
          <li>
            <svg viewBox="0 0 16 16" aria-hidden="true"><rect x="1" y="3" width="14" height="10" fill="#fff"/><path d="M1 3l7 6 7-6" fill="none" stroke="#ee4540" stroke-width="1.4"/></svg>
            hello@kinfolksteam.com
          </li>
          <li>
            <svg viewBox="0 0 16 16" aria-hidden="true"><circle cx="8" cy="8" r="6.5" fill="none" stroke="#fff" stroke-width="1.5"/><ellipse cx="8" cy="8" rx="3" ry="6.5" fill="none" stroke="#fff" stroke-width="1.2"/><path d="M1.5 8h13M2.5 5h11M2.5 11h11" stroke="#fff" stroke-width="1.1"/></svg>
            www.kinfolksteam.com
          </li>
        </ul>
      </div>
      <p class="address">18 Birchwood Lane, Millbrook, 45018</p>
    </div>
  </section>

</body>
</html>
```